Business Card Design For Office Furniture Clearance Company

Kestrel Office Clearance - our company name pretty much explains what we do, we clear offices for high end clients, mainly plc's and large international companies.

We require a nice looking business card that displays professionalism but without being too serious.

It would be nice to see just a little more than a conventional boring business card, make sure you add some flare.

Industry/Entity Type

Office Furniture

Contact Information for Business Card

CARD 1

Mark Holloway
Director
mark@kestrelofficeclearance.co.uk
m: 07700 153928

t: 01632 960418
www.kestrelofficeclearance.co.uk

Kestrel Office Clearance
Unit K4 B
2-8 Fenwick Lane
Thornwick
Elmsbury Vale
ZZ9 4QT

clear offices, zero fuss… we take care of the lot.

CARD 2

Peter Radford
Director
peter@kestrelofficeclearance.co.uk
m: 07700 382615

t: 01632 960418

Kestrel Office Clearance
Unit K4 B
2-8 Fenwick Lane
Thornwick
Elmsbury Vale
ZZ9 4QT

Font styles to use
Sans Serif

Requirements
Must have
• A white background - as we have a blue logo.
Nice to have
• Nice use of the logo - play around with this and dissect it.

```html
<!DOCTYPE html>
<html lang="en">
<head>
<meta charset="utf-8">
<title>Kestrel Office Clearance – Business Card</title>
<link href="https://fonts.googleapis.com/css2?family=Source+Sans+3:wght@400;600;700&display=swap" rel="stylesheet">
<style>
  :root {
    --stage: #141414;
    --card-white: #ffffff;
    --card-blue: #065f8f;
    --brand-blue: #0a74bb;
    --ink: #222222;
  }
  * { margin: 0; padding: 0; box-sizing: border-box; }
  html, body { width: 1200px; height: 900px; overflow: hidden; }
  body {
    background: linear-gradient(180deg, #262626 0%, var(--stage) 60%, #0a0a0a 100%);
    font-family: "Source Sans 3", Arial, sans-serif;
    position: relative;
  }
  .card {
    position: absolute;
    top: 306px;
    height: 271px;
    border-radius: 10px;
  }
  .card--front { left: 149px; width: 439px; background: var(--card-white); }
  .card--back { left: 608px; width: 441px; background: var(--card-blue); }

  .brand-disc {
    position: absolute;
    border-radius: 50%;
    display: flex;
    align-items: center;
    justify-content: center;
    font-weight: 700;
  }
  .card--front .brand-disc {
    left: 38px; top: 44px; width: 154px; height: 154px;
    background: var(--brand-blue);
    color: var(--card-white);
    font-size: 30px;
  }
  .card--back .brand-disc {
    left: 133px; top: 49px; width: 174px; height: 174px;
    background: var(--card-white);
    color: var(--card-blue);
    font-size: 32px;
  }

  .contact { position: absolute; left: 221px; top: 32px; color: var(--ink); }
  .contact__name { font-size: 16px; font-weight: 600; color: var(--brand-blue); line-height: 20px; }
  .contact__role { font-size: 12px; line-height: 14px; }
  .contact__company { margin-top: 10px; font-size: 14px; font-weight: 700; color: var(--brand-blue); line-height: 18px; }
  .contact__address { font-size: 12.5px; line-height: 16px; }
  .contact__list { list-style: none; margin-top: 11px; font-size: 12.5px; line-height: 15.7px; }
  .contact__list li { display: flex; align-items: center; gap: 7px; }
  .contact__list svg { width: 9px; height: 9px; fill: var(--brand-blue); flex: none; }

  .tagline {
    position: absolute; left: 0; right: 0; top: 220px;
    text-align: center;
    font-size: 14px; font-weight: 600;
    color: var(--brand-blue);
  }
</style>
</head>
<body>
  <section class="card card--front" aria-label="Business card front">
    <div class="brand-disc">Kestrel</div>
    <div class="contact">
      <p class="contact__name">Mark Holloway</p>
      <p class="contact__role">Director</p>
      <p class="contact__company">Kestrel Office Clearance</p>
      <p class="contact__address">Unit K4 B,2-8 Fenwick Lane<br>Thornwick,Elmsbury Vale,ZZ9 4QT</p>
      <ul class="contact__list">
        <li><svg viewBox="0 0 10 10" aria-hidden="true"><path d="M3 0h4a1 1 0 0 1 1 1v8a1 1 0 0 1-1 1H3a1 1 0 0 1-1-1V1a1 1 0 0 1 1-1zm0 1.5v6h4v-6z"/></svg>07700 153928</li>
        <li><svg viewBox="0 0 10 10" aria-hidden="true"><path d="M2 0.5l1.8 2-1 1.2c.6 1.3 1.6 2.3 2.9 2.9l1.2-1 2 1.8-1.2 1.8C4.5 9 1 5.5.3 1.7z"/></svg>01632 960418</li>
        <li><svg viewBox="0 0 10 10" aria-hidden="true"><path d="M0 2h10v.8L5 5.6 0 2.8zm0 1.9l5 2.8 5-2.8V8H0z"/></svg>mark@kestrelofficeclearance.co.uk</li>
        <li><svg viewBox="0 0 10 10" aria-hidden="true"><circle cx="5" cy="5" r="4.6"/></svg>www.kestrelofficeclearance.co.uk</li>
      </ul>
    </div>
    <p class="tagline">clear offices, zero fuss… we take care of the lot.</p>
  </section>

  <section class="card card--back" aria-label="Business card back">
    <div class="brand-disc">Kestrel</div>
  </section>
</body>
</html>
```